Business Card Design

We like to use greens as you will see in our logo (but not TOO much green). We are a Dental Clinic in a somewhat eccentric community. We do not like the dated sharp designs which we see many dentists use. We're looking for something bright and fresh while still maintaining the integrity of the profession. Elegance is not necessarily what we are going for... we need for the design to be "mature" but also up-lifting.

See our logo.
Updates

Project Deadline Extended
Reason: We have 5 designs which we like. But we'd like to see a few more before committing to a design.

Project Deadline Extended
Reason: We are awaiting revisions to this project. We are still welcoming designs while we wait to see if designers are able to provide to us the revisions we require in order to proceed with a selection.

Target Market(s)

Younger families - ages late 20's to early 40's

Industry/Entity Type

Business

Contact Information for Business Card

Corwel T. Banfry DDS 2730 W. Halvert Rd. Ste. 7 Royal Oak, MI 48391 (248)555-0174 FX (248)555-0189 info@BrightwellDentalCareMi.com BrigthwellDentalCareMi.com on the back of the card we need an appointment reminder (For____ Date___ Time____) with "If you are unable to keep your appointment, kindly give 48 hours notice" at the bottom. No use of teeth in the design. DOUBLE SIDED DESIGN

Requirements
Should not have
• The use of pictures of teeth

```html
<!DOCTYPE html>
<html lang="en">
<head>
<meta charset="utf-8">
<title>Brightwell Dental Care – Business Card</title>
<link rel="stylesheet" href="https://fonts.googleapis.com/css2?family=Source+Sans+3:ital,wght@0,400;0,600;0,700;1,400&family=Marcellus&display=swap">
<style>
  :root {
    --green-dark: #1e6b34;
    --green-light: #8dc63f;
    --ink: #231f20;
    --line: #555555;
    --paper: #ffffff;
    --backdrop: #e8e4dd;
  }
  * { box-sizing: border-box; margin: 0; padding: 0; }
  html, body { width: 1200px; height: 1179px; overflow: hidden; }
  body {
    background: var(--backdrop);
    position: relative;
    font-family: "Source Sans 3", "Helvetica Neue", Arial, sans-serif;
    color: var(--ink);
  }
  .card {
    position: absolute;
    background: var(--paper);
    border: 1.5px solid #333;
    overflow: hidden;
  }
  /* ---------- Front ---------- */
  .card--front { left: 242px; top: 46px; width: 912px; height: 523px; }
  .front__accent-bar {
    position: absolute; left: 0; top: 0;
    width: 647px; height: 23px;
    background: var(--green-light);
  }
  .brand {
    position: absolute;
    display: flex; align-items: center; gap: 18px;
    color: var(--green-dark);
    font-weight: 600;
    line-height: 0.95;
  }
  .brand__dot {
    flex: none;
    border-radius: 50%;
    background: var(--green-light);
  }
  .brand--front { left: 62px; top: 95px; font-size: 68px; }
  .brand--front .brand__dot { width: 58px; height: 58px; }
  .contact {
    position: absolute; right: 36px; top: 252px;
    text-align: right;
    font-size: 21px; line-height: 30px;
  }
  .contact__address { margin-bottom: 12px; }
  .contact__row {
    display: flex; justify-content: flex-end; align-items: center; gap: 7px;
    margin-bottom: 9px;
  }
  .contact__row svg { width: 17px; height: 17px; fill: var(--ink); }
  .front__web-bar {
    position: absolute; right: 0; bottom: 0;
    width: 484px; height: 58px;
    background: var(--green-dark);
    color: var(--paper);
    display: flex; align-items: center; justify-content: center;
    font-size: 23px; letter-spacing: 1.6px;
  }
  /* ---------- Back ---------- */
  .card--back { left: 30px; top: 611px; width: 916px; height: 525px; }
  .brand--back { left: 73px; top: 42px; font-size: 40px; gap: 12px; }
  .brand--back .brand__dot { width: 34px; height: 34px; }
  .appointment__title {
    position: absolute; left: 76px; top: 168px;
    font-family: "Marcellus", Georgia, serif;
    font-size: 35px; letter-spacing: 0.5px;
    color: var(--green-dark);
  }
  .field {
    position: absolute;
    font-size: 25px; color: #333;
    display: flex; align-items: baseline; gap: 10px;
  }
  .field__line {
    display: inline-block; height: 0;
    border-bottom: 2px dotted var(--line);
  }
  .field--name { left: 80px; top: 247px; }
  .field--name .field__line { width: 510px; margin-left: 10px; }
  .field--date { left: 80px; top: 311px; }
  .field--date .field__line { width: 165px; margin-left: 20px; }
  .field--date .field__line--time { width: 155px; margin-left: 0; }
  .field--next { left: 80px; top: 376px; align-items: center; }
  .entry-box {
    display: inline-block;
    width: 165px; height: 35px;
    border: 1.5px solid #444; border-radius: 4px;
  }
  .field--next .entry-box:first-of-type { margin-left: 14px; }
  .field--next .entry-box + .entry-box { margin-left: 22px; }
  .days {
    position: absolute; right: 26px; top: 78px;
    list-style: none;
  }
  .days__item {
    position: absolute; right: 0;
    display: flex; align-items: center; gap: 14px;
    font-weight: 700; font-size: 25px; color: #333;
    font-family: Arial, "Helvetica Neue", sans-serif;
  }
  .days__item .entry-box { width: 56px; height: 34px; }
  .notice {
    position: absolute; left: 0; right: 0; top: 450px;
    text-align: center;
    font-style: italic; font-size: 25px;
  }
  .back__base-bar {
    position: absolute; left: 0; right: 0; bottom: 0;
    height: 12px; background: var(--green-dark);
  }
</style>
</head>
<body>

<section class="card card--front" aria-label="Business card front">
  <div class="front__accent-bar"></div>
  <div class="brand brand--front">
    <span class="brand__dot"></span>
    <span class="brand__name">Brightwell<br>Dental Care</span>
  </div>
  <address class="contact" style="font-style:normal">
    <div class="contact__address">2730 W. Halvert Rd.<br>Ste. 7 Royal Oak, MI 48391</div>
    <div class="contact__row">
      <svg viewBox="0 0 24 24" aria-hidden="true"><path d="M6.6 10.8a15.1 15.1 0 0 0 6.6 6.6l2.2-2.2c.3-.3.7-.4 1-.2 1.1.4 2.3.6 3.6.6.6 0 1 .4 1 1V20c0 .6-.4 1-1 1A17 17 0 0 1 3 4c0-.6.4-1 1-1h3.5c.6 0 1 .4 1 1 0 1.3.2 2.5.6 3.6.1.3 0 .7-.2 1z"/></svg>
      <span>(248)555-0174</span>
    </div>
    <div class="contact__row">
      <svg viewBox="0 0 24 24" aria-hidden="true"><path d="M6 3h10l2 2v4H6zM3 10h18v8h-3v3H6v-3H3zm5 6v3h8v-3z"/></svg>
      <span>(248)555-0189</span>
    </div>
    <div class="contact__row">
      <svg viewBox="0 0 24 24" aria-hidden="true"><path d="M2 9l10-6 10 6v12H2zm2 1.2V19h16v-8.8l-8 5z"/></svg>
      <span>info@BrightwellDentalCareMi.com</span>
    </div>
  </address>
  <div class="front__web-bar">www.BrigthwellDentalCareMi.com</div>
</section>

<section class="card card--back" aria-label="Business card back: appointment reminder">
  <div class="brand brand--back">
    <span class="brand__dot"></span>
    <span class="brand__name">Brightwell<br>Dental Care</span>
  </div>
  <h2 class="appointment__title" style="font-weight:400">YOUR APPOINTMENT</h2>

  <div class="field field--name">Name :<span class="field__line"></span></div>
  <div class="field field--date">Date :<span class="field__line"></span>Time :<span class="field__line field__line--time"></span>am / pm</div>
  <div class="field field--next">Next Appointment<span class="entry-box"></span><span class="entry-box"></span></div>

  <ul class="days">
    <li class="days__item" style="top:0">MON<span class="entry-box"></span></li>
    <li class="days__item" style="top:63px">TUE<span class="entry-box"></span></li>
    <li class="days__item" style="top:127px">WED<span class="entry-box"></span></li>
    <li class="days__item" style="top:191px">THU<span class="entry-box"></span></li>
    <li class="days__item" style="top:248px">FRI<span class="entry-box"></span></li>
    <li class="days__item" style="top:303px">SAT<span class="entry-box"></span></li>
  </ul>

  <p class="notice">If you are unable to keep your appointment, kindly give 48 hours notice</p>
  <div class="back__base-bar"></div>
</section>

</body>
</html>
```